Tour operator needs simple coded WordPress site (updated extra payment for coding and guaranteed)

[update 9/7/2015]
If you design a new logo and it gets accepted, even if we use another template with your logo you will get $50
[update 8/7/2015]
Update on questions about dual-language
For dual languages we are happy to set up a second site with the same designs in a second language.
For the design aspect just allow the user to switch between languages with an icon.
For the coding, a replica of the site on a second server will do (to save messing around with multiple language plugins) - we will populate it with Chinese text
[original post]
Simple coded WordPress site for tours
You can choose to design only or design and code ($340 design, $150 bonus for coding)
Open design brief - use your creativity
Will be in 2 languages (English and Chinese) but design needs only to be in one language
Winning design will be chosen only from home page, but the winner must make a second standard template page when chosen at no extra cost.
Must be responsive design
We only need homepage and standard template page design and coding, we will populate the pages
You can use design ideas from our pamphlet if you like - attached
Only a sample logo and colors on website and pamphlet - feel free to change as the current ones seem restrictive
Current website framework only to give an idea of the number of pages and basic menu structure (no need to use existing navigation style or any style at all for that matter, open brief)
http://brightwattlejourneys.com.au/
Target Market(s)
Chinese parents of kids 10-14 (the kids will take the tour)
Industry/Entity Type
Tour
Number of Pages Required
2 page
Look and feel
Each slider illustrates characteristics of the customer's brand and the style your logo design should communicate.

```html
<!DOCTYPE html>
<html lang="en">
<head>
<meta charset="utf-8">
<title>Bright Wattle Journeys</title>
<link href="https://fonts.googleapis.com/css2?family=Oswald:wght@400;500&family=Lato:wght@400;700&display=swap" rel="stylesheet">
<style>
:root{
  --navy:#2e3a7a;
  --navy-band:#34407a;
  --gold:#f2ae1c;
  --ink:#333333;
  --text:#555555;
  --muted:#8a8a8a;
  --line:#cfcfcf;
  --panel:#efefef;
  --footer:#1f1f1f;
  --white:#ffffff;
}
*{box-sizing:border-box;margin:0;padding:0}
html,body{width:926px;height:1200px;overflow:hidden;background:var(--white)}
body{position:relative;font-family:'Lato',sans-serif;color:var(--text)}
.abs{position:absolute}

/* hero */
.hero{left:0;top:0;width:926px;height:476px;overflow:hidden}
.hero-photo{position:absolute;inset:0;background:linear-gradient(180deg,#7d838c 0%,#5d6168 35%,#4a4d52 65%,#3a3c40 100%)}
.lang-select{left:748px;top:15px;width:78px;height:24px;border:2px solid var(--white);color:var(--white);font-weight:700;font-size:12px;line-height:20px;padding-left:8px}
.lang-select svg{position:absolute;right:7px;top:6px}
.slide-arrow{top:199px}
.brand-box{left:102px;top:304px;width:215px;height:109px;background:var(--white);display:flex;align-items:center;justify-content:center;gap:8px}
.brand-dot{width:14px;height:14px;border-radius:50%;background:var(--gold)}
.brand-name{font-family:'Oswald',sans-serif;font-weight:500;font-size:19px;color:var(--navy);line-height:1.1;text-transform:uppercase}
.tagline{right:103px;top:362px;width:460px;text-align:right;font-family:'Oswald',sans-serif;font-size:22px;line-height:28px;color:var(--white);text-transform:uppercase}
.nav-rule{left:0;top:428px;width:926px;height:1px;background:rgba(255,255,255,.45)}
.main-nav{left:102px;top:429px;height:47px;display:flex}
.main-nav a{display:block;width:120px;text-align:center;line-height:47px;font-size:12px;font-weight:700;color:var(--white);text-decoration:none}
.main-nav a.active{width:111px;background:var(--white);color:var(--navy)}
.social{top:437px;width:31px;height:31px;border:2px solid var(--white);border-radius:50%}

/* welcome */
.welcome{left:102px;top:520px;width:455px}
.section-title{font-family:'Oswald',sans-serif;font-weight:400;font-size:23px;color:var(--ink);text-transform:uppercase;line-height:30px}
.section-title .navy{color:var(--navy)}
.section-title .gold{color:var(--gold)}
.welcome .section-title{border-bottom:1px solid var(--line);padding-bottom:4px}
.lead{font-weight:700;font-size:12px;line-height:15.5px;color:#4a4a4a;margin-top:8px}
.body-copy{font-size:10.3px;line-height:13.5px;color:#666;margin-top:5px}
.btn{display:block;background:var(--navy);color:var(--white);font-weight:700;font-size:14px;text-align:center;text-transform:uppercase;line-height:26px;width:105px;height:26px}
.divider-v{left:575px;top:506px;width:1px;height:210px;background:#e3e3e3}
.inquiry{left:598px;top:520px;width:227px}
.field{border:1px solid #c8c8c8;height:26px;margin-top:6px;font-size:11px;color:#999;padding:6px 7px}
.field.first{margin-top:12px}
.field.area{height:58px}

/* features */
.features{left:0;top:732px;width:926px;height:381px;background:var(--panel)}
.card{top:39px;height:305px;background:var(--white);border:1px solid #dcdcdc;border-top:3px solid var(--gold);padding:14px 14px}
.card-head{display:flex;align-items:flex-end;gap:8px}
.card-title{flex:1;font-family:'Oswald',sans-serif;font-size:17px;color:var(--navy);text-transform:uppercase;border-bottom:1px dotted #aaa;padding-bottom:1px;line-height:22px}
.card ul{list-style:none;margin-top:10px}
.card li{position:relative;padding-left:24px;font-size:10.3px;line-height:13.4px;color:#666;margin-bottom:7px}
.card li svg{position:absolute;left:0;top:1px}

/* newsletter + footer */
.newsletter{left:0;top:1113px;width:926px;height:43px;background:var(--navy-band);color:var(--white)}
.nl-icon{left:102px;top:5px;width:33px;height:33px;border:2px solid var(--white);border-radius:50%}
.nl-title{left:145px;top:9px;font-size:19px;line-height:24px}
.nl-sub{left:390px;top:14px;font-size:11.5px}
.nl-input{left:571px;top:11px;width:189px;height:22px;background:var(--white);color:#444;font-size:10px;padding:5px 7px}
.nl-btn{left:767px;top:11px;width:58px;height:22px;background:#111;color:var(--white);font-size:10px;font-weight:700;text-align:center;line-height:22px;border:1px solid #555}
.footer{left:0;top:1156px;width:926px;height:44px;background:var(--footer);color:var(--white);font-size:10px}
.footer-links{left:102px;top:16px}
.footer-links span{margin:0 5px;color:#ccc}
.copyright{right:103px;top:16px}
</style>
</head>
<body>

<header class="hero abs">
  <div class="hero-photo" role="img" aria-label="Photo of a cheerful group of students posing by the harbour with a bridge behind them"></div>
  <div class="lang-select abs">English
    <svg width="10" height="7" viewBox="0 0 10 7"><path d="M1 1l4 4 4-4" fill="none" stroke="#fff" stroke-width="1.6"/></svg>
  </div>
  <svg class="slide-arrow abs" style="left:62px" width="41" height="78" viewBox="0 0 41 78"><path d="M40 1L1 39l39 38" fill="none" stroke="#fff" stroke-width="1.2"/></svg>
  <svg class="slide-arrow abs" style="left:825px" width="41" height="78" viewBox="0 0 41 78"><path d="M1 1l39 38L1 77" fill="none" stroke="#fff" stroke-width="1.2"/></svg>
  <div class="brand-box abs"><span class="brand-dot"></span><span class="brand-name">Bright Wattle<br>Journeys</span></div>
  <p class="tagline abs">Educational, safe, culturally Bright Wattle Journeys exchange enlightening and fun.</p>
  <div class="nav-rule abs"></div>
  <nav class="main-nav abs">
    <a class="active" href="#">Home</a><a href="#">About Us</a><a href="#">Tours</a><a href="#">Contact Us</a>
  </nav>
  <span class="social abs" style="left:714px" aria-label="Social link"></span>
  <span class="social abs" style="left:754px" aria-label="Social link"></span>
  <span class="social abs" style="left:794px" aria-label="Social link"></span>
</header>

<section class="welcome abs">
  <h1 class="section-title">Welcome to <span class="navy">Bright</span> <span class="gold">Wattle</span> <span class="navy">Journeys</span></h1>
  <p class="lead">At Bright Wattle Journeys we are passionate about educational travel and opportunities for students to gain academic and cultural understanding of Australia.</p>
  <p class="body-copy">14 day premium cultural and educational tours to Australian cities. Educational, safe, culturally enlightening and fun. Learn about educational institutions, history, sports, laws and customs, food and culture while improving your English.</p>
  <p class="body-copy">At Bright Wattle Journeys we are passionate about educational travel and providing opportunities for students to learn more about a country and gain a deeper understanding of the culture. The out of classroom experience gained on our trips is invaluable.</p>
  <a class="btn" style="margin:9px 0 0 auto" href="#">Read More</a>
</section>
<div class="divider-v abs"></div>
<section class="inquiry abs">
  <h2 class="section-title">Quick Inquiry</h2>
  <div class="field first">Name</div>
  <div class="field">Email</div>
  <div class="field area">Message</div>
  <a class="btn" style="margin:7px 0 0 auto" href="#">Submit</a>
</section>

<section class="features abs">
  <div class="card abs" style="left:102px;width:347px">
    <div class="card-head">
      <svg width="30" height="20" viewBox="0 0 30 20"><path d="M15 1L1 7l14 6 14-6z" fill="#f2ae1c"/><path d="M7 10v6c3 3 13 3 16 0v-6l-8 3z" fill="#f2ae1c"/><path d="M26 8v8" stroke="#f2ae1c" stroke-width="1.5"/></svg>
      <h3 class="card-title">Educational and Cultural</h3>
    </div>
    <ul>
      <li><svg width="18" height="11" viewBox="0 0 18 11"><path d="M1 10C3 4 8 3 12 3V0l6 5-6 5V7C8 7 4 7 1 10z" fill="#2e3a7a"/></svg>Professional lecturers from Sydney universities</li>
      <li><svg width="18" height="11" viewBox="0 0 18 11"><path d="M1 10C3 4 8 3 12 3V0l6 5-6 5V7C8 7 4 7 1 10z" fill="#2e3a7a"/></svg>2 hour lessons every day in easy to understand,<br>high-quality English</li>
      <li><svg width="18" height="11" viewBox="0 0 18 11"><path d="M1 10C3 4 8 3 12 3V0l6 5-6 5V7C8 7 4 7 1 10z" fill="#2e3a7a"/></svg>Subjects from the Australian Educational Curriculum as well as cultural information on Australia</li>
      <li><svg width="18" height="11" viewBox="0 0 18 11"><path d="M1 10C3 4 8 3 12 3V0l6 5-6 5V7C8 7 4 7 1 10z" fill="#2e3a7a"/></svg>How to live, get around, shop and socialise in Australia</li>
      <li><svg width="18" height="11" viewBox="0 0 18 11"><path d="M1 10C3 4 8 3 12 3V0l6 5-6 5V7C8 7 4 7 1 10z" fill="#2e3a7a"/></svg>Attitudes to languages, food, religion and culture</li>
      <li><svg width="18" height="11" viewBox="0 0 18 11"><path d="M1 10C3 4 8 3 12 3V0l6 5-6 5V7C8 7 4 7 1 10z" fill="#2e3a7a"/></svg>Outdoor activities and sport</li>
    </ul>
  </div>
  <div class="card abs" style="left:478px;width:347px">
    <div class="card-head">
      <svg width="22" height="26" viewBox="0 0 22 26"><path d="M5 11V7a6 6 0 0112 0v4" fill="none" stroke="#f2ae1c" stroke-width="3"/><rect x="1" y="11" width="20" height="14" rx="1" fill="#f2ae1c"/><circle cx="11" cy="17" r="2" fill="#fff"/></svg>
      <h3 class="card-title" style="margin-left:10px">Safe and Secure</h3>
    </div>
    <ul>
      <li><svg width="18" height="11" viewBox="0 0 18 11"><path d="M1 10C3 4 8 3 12 3V0l6 5-6 5V7C8 7 4 7 1 10z" fill="#2e3a7a"/></svg>Staff certified by the government for Working With Children</li>
      <li><svg width="18" height="11" viewBox="0 0 18 11"><path d="M1 10C3 4 8 3 12 3V0l6 5-6 5V7C8 7 4 7 1 10z" fill="#2e3a7a"/></svg>Staff certified in first aid care</li>
      <li><svg width="18" height="11" viewBox="0 0 18 11"><path d="M1 10C3 4 8 3 12 3V0l6 5-6 5V7C8 7 4 7 1 10z" fill="#2e3a7a"/></svg>Professional accommodation with excellent history in caring for children with extremely well documented Safety Management Procedures including;</li>
      <li><svg width="18" height="11" viewBox="0 0 18 11"><path d="M1 10C3 4 8 3 12 3V0l6 5-6 5V7C8 7 4 7 1 10z" fill="#2e3a7a"/></svg>Safety Management - reducing risk when taking students out of the classroom</li>
      <li><svg width="18" height="11" viewBox="0 0 18 11"><path d="M1 10C3 4 8 3 12 3V0l6 5-6 5V7C8 7 4 7 1 10z" fill="#2e3a7a"/></svg>Safety &amp; Emergency Procedures (Location-specific)</li>
      <li><svg width="18" height="11" viewBox="0 0 18 11"><path d="M1 10C3 4 8 3 12 3V0l6 5-6 5V7C8 7 4 7 1 10z" fill="#2e3a7a"/></svg>Standard Operating Procedures</li>
      <li><svg width="18" height="11" viewBox="0 0 18 11"><path d="M1 10C3 4 8 3 12 3V0l6 5-6 5V7C8 7 4 7 1 10z" fill="#2e3a7a"/></svg>Activity-Specific Risk Management Matrix</li>
      <li><svg width="18" height="11" viewBox="0 0 18 11"><path d="M1 10C3 4 8 3 12 3V0l6 5-6 5V7C8 7 4 7 1 10z" fill="#2e3a7a"/></svg>Area Assessment Documentation</li>
      <li><svg width="18" height="11" viewBox="0 0 18 11"><path d="M1 10C3 4 8 3 12 3V0l6 5-6 5V7C8 7 4 7 1 10z" fill="#2e3a7a"/></svg>Medical Form, Dietary Requirements Form ,First Aid Incident &amp; Management Forms</li>
      <li><svg width="18" height="11" viewBox="0 0 18 11"><path d="M1 10C3 4 8 3 12 3V0l6 5-6 5V7C8 7 4 7 1 10z" fill="#2e3a7a"/></svg>Clothing &amp; Equipment List</li>
    </ul>
  </div>
</section>

<section class="newsletter abs">
  <span class="nl-icon abs"><svg width="29" height="29" viewBox="0 0 29 29"><rect x="7" y="9" width="15" height="11" fill="#fff"/><path d="M7 9l7.5 6L22 9" fill="none" stroke="#34407a" stroke-width="1.4"/></svg></span>
  <span class="nl-title abs">Newsletter Signup</span>
  <svg class="abs" style="left:344px;top:4px" width="28" height="35" viewBox="0 0 28 35"><path d="M2 1l16 16.5L2 34M9 1l16 16.5L9 34" fill="none" stroke="#fff" stroke-width="1.3"/></svg>
  <span class="nl-sub abs">Signup For Free Email Updates</span>
  <span class="nl-input abs">Enter your email here</span>
  <span class="nl-btn abs">SUBMIT</span>
</section>

<footer class="footer abs">
  <div class="footer-links abs">Home<span>|</span>About Us<span>|</span>Tours<span>|</span>Contact Us</div>
  <div class="copyright abs">© 2015 BRIGHT WATTLE JOURNEYS. &nbsp;| &nbsp;All Rights Reserved.</div>
</footer>

</body>
</html>
```